Business Card Design

I already have a company logo for my company. I have a logo for the manufacturer we represent. I want a professional business card design.

```html
<!DOCTYPE html>
<html lang="en">
<head>
<meta charset="utf-8">
<title>Business Card – Beacon Alert Co</title>
<link rel="stylesheet" href="https://fonts.googleapis.com/css2?family=Exo+2:wght@400;700&display=swap">
<style>
  :root {
    --backdrop: #2e2e30;
    --card-black: #1b1b1c;
    --card-black-deep: #111112;
    --brand-red: #e3202a;
    --rim-grey: #8d8d8f;
    --rim-red: #f0343d;
    --accent-gold: #e2b20f;
    --ink-white: #ffffff;
  }
  * { box-sizing: border-box; margin: 0; padding: 0; }
  html, body {
    width: 1200px; height: 982px; overflow: hidden;
    background: var(--backdrop);
    font-family: "Exo 2", sans-serif;
  }
  .canvas { position: relative; width: 1200px; height: 982px; }

  .card {
    position: absolute; width: 620px; height: 354px; overflow: hidden;
    box-shadow: 0 14px 30px rgba(0,0,0,.45);
  }

  /* back side */
  .card-back {
    left: 490px; top: 70px;
    background: linear-gradient(135deg, var(--card-black) 0%, var(--card-black-deep) 100%);
    display: flex; align-items: center; justify-content: center;
  }

  /* front side */
  .card-front { left: 130px; top: 520px; background: var(--brand-red); }
  .front-curve { position: absolute; inset: 0; }

  .identity {
    position: absolute; left: 52px; top: 40px; color: var(--ink-white);
  }
  .identity-name { font-size: 30px; font-weight: 700; letter-spacing: 1px; line-height: 1; }
  .identity-title { font-size: 16px; font-weight: 400; margin-top: 6px; letter-spacing: .5px; }

  .contact-list {
    position: absolute; left: 42px; top: 130px; list-style: none; color: var(--ink-white);
    font-size: 15px; line-height: 1.25;
  }
  .contact-item { display: flex; align-items: flex-start; gap: 10px; margin-bottom: 6px; }
  .contact-icon { width: 14px; height: 14px; flex: none; margin-top: 2px; fill: var(--ink-white); }

  /* brand name stand-in */
  .brand { display: flex; align-items: center; gap: 12px; }
  .brand-dot { width: 22px; height: 22px; border-radius: 50%; background: var(--accent-gold); flex: none; }
  .brand-name {
    font-weight: 700; color: var(--ink-white); letter-spacing: 2px; text-transform: uppercase;
    line-height: 1;
  }
  .card-back .brand-name { font-size: 40px; }
  .card-front .brand { position: absolute; left: 400px; top: 158px; }
  .card-front .brand-name { font-size: 26px; }
  .card-front .brand-dot { width: 16px; height: 16px; }
</style>
</head>
<body>
<main class="canvas">

  <section class="card card-back" aria-label="Card back">
    <div class="brand">
      <span class="brand-dot"></span>
      <span class="brand-name">Beacon Alert Co</span>
    </div>
  </section>

  <section class="card card-front" aria-label="Card front">
    <svg class="front-curve" viewBox="0 0 620 354" width="620" height="354" aria-hidden="true">
      <path d="M372 0 Q300 170 412 354 L620 354 L620 0 Z" fill="var(--rim-red)"/>
      <path d="M380 0 Q310 170 420 354 L620 354 L620 0 Z" fill="var(--rim-grey)"/>
      <path d="M392 0 Q324 170 432 354 L620 354 L620 0 Z" fill="var(--card-black)"/>
    </svg>

    <div class="identity">
      <h1 class="identity-name">JOHN SMITH</h1>
      <p class="identity-title">Founder &amp; CEO</p>
    </div>

    <ul class="contact-list">
      <li class="contact-item">
        <svg class="contact-icon" viewBox="0 0 24 24"><path d="M12 2a7 7 0 0 0-7 7c0 5 7 13 7 13s7-8 7-13a7 7 0 0 0-7-7zm0 9.5A2.5 2.5 0 1 1 12 6.5a2.5 2.5 0 0 1 0 5z"/></svg>
        <span>423 Street Address, City<br>State &amp; ZIP Code Country</span>
      </li>
      <li class="contact-item">
        <svg class="contact-icon" viewBox="0 0 24 24"><path d="M6.6 10.8a15 15 0 0 0 6.6 6.6l2.2-2.2c.3-.3.7-.4 1-.2 1.1.4 2.3.6 3.6.6.6 0 1 .4 1 1V20c0 .6-.4 1-1 1A17 17 0 0 1 3 4c0-.6.4-1 1-1h3.5c.6 0 1 .4 1 1 0 1.3.2 2.5.6 3.6.1.3 0 .7-.2 1z"/></svg>
        <span>(123) 456-7890</span>
      </li>
      <li class="contact-item">
        <svg class="contact-icon" viewBox="0 0 24 24"><path d="M7 1h10a2 2 0 0 1 2 2v18a2 2 0 0 1-2 2H7a2 2 0 0 1-2-2V3a2 2 0 0 1 2-2zm0 3v14h10V4z"/></svg>
        <span>(123) 456-7890</span>
      </li>
      <li class="contact-item">
        <svg class="contact-icon" viewBox="0 0 24 24"><path d="M6 2h12v5H6zM4 8h16a2 2 0 0 1 2 2v7h-4v5H6v-5H2v-7a2 2 0 0 1 2-2zm4 8v4h8v-4z"/></svg>
        <span>(123) 456-7890</span>
      </li>
      <li class="contact-item">
        <svg class="contact-icon" viewBox="0 0 24 24"><path d="M2 4h20v16H2zm2 2v.5l8 5 8-5V6zm0 3v9h16V9l-8 5z"/></svg>
        <span>info@yourwebsitehere.com</span>
      </li>
      <li class="contact-item">
        <svg class="contact-icon" viewBox="0 0 24 24"><path d="M12 2a10 10 0 1 0 0 20 10 10 0 0 0 0-20zm6.9 9h-3a15 15 0 0 0-1.3-6A8 8 0 0 1 18.9 11zM12 4c1 1.3 1.8 4 1.9 7h-3.8C10.2 8 11 5.3 12 4zM9.4 5A15 15 0 0 0 8.1 11h-3A8 8 0 0 1 9.4 5zM5.1 13h3a15 15 0 0 0 1.3 6A8 8 0 0 1 5.1 13zM12 20c-1-1.3-1.8-4-1.9-7h3.8c-.1 3-.9 5.7-1.9 7zm2.6-1a15 15 0 0 0 1.3-6h3a8 8 0 0 1-4.3 6z"/></svg>
        <span>yourwebsitehere.com</span>
      </li>
    </ul>

    <div class="brand">
      <span class="brand-dot"></span>
      <span class="brand-name">Beacon Alert Co</span>
    </div>
  </section>

</main>
</body>
</html>
```